Business Card Design

Just looking for a good designs that looks good with our company logo. I'd like it to be simple and to the point. Just including contact information, our logo, and my name somewhere on the card so future clients know who they're contacting, and a couple services offered. The two images I attached are pictures of our logo. I don't care which color they they are, I just attached both images to give a reference of logo colors depending on the color of the card.
Names: Carl Whitby
Phone: 816-555-0147
Email: greenstripeyard@fernmail.test
Services offered:
Mowing
Fertilization
Aeration
Bed & tree maintenance
and more.
Business
Names: Carl Whitby
Phone: 816-555-0147
(no website)

```html
<!DOCTYPE html>
<html lang="en">
<head>
<meta charset="utf-8">
<title>Greenstripe Yard Care – Business Card</title>
<link href="https://fonts.googleapis.com/css2?family=Lato:wght@400;700;900&display=swap" rel="stylesheet">
<style>
  :root {
    --stage: #2a2a2a;
    --card-white: #f7f7f7;
    --brand-orange: #e0482e;
    --brand-navy: #2b3043;
    --divider-grey: #5a5a5a;
    --services-grey: #cfcac6;
  }
  * { box-sizing: border-box; margin: 0; padding: 0; }
  html, body {
    width: 1200px; height: 900px; overflow: hidden;
    background: var(--stage);
    font-family: "Lato", sans-serif;
  }
  .business-card {
    position: absolute;
    left: 100px; top: 164px;
    width: 1000px; height: 572px;
    background: var(--card-white);
    box-shadow: 0 18px 40px rgba(0,0,0,.5);
    overflow: hidden;
  }
  .brand {
    position: absolute;
    left: 70px; top: 170px;
    display: flex; align-items: center; gap: 18px;
  }
  .brand-dot {
    width: 46px; height: 46px; border-radius: 50%;
    background: var(--brand-orange);
  }
  .brand-name {
    font-weight: 900; font-size: 40px; line-height: 1.05;
    color: var(--brand-navy); text-transform: uppercase;
    letter-spacing: 1px;
  }
  .holder {
    position: absolute; left: 600px; top: 92px;
  }
  .holder-name {
    font-weight: 700; font-size: 28px; color: var(--brand-navy);
    letter-spacing: .5px; text-transform: uppercase;
  }
  .holder-role {
    font-weight: 700; font-size: 18px; color: var(--brand-orange);
    text-transform: uppercase; letter-spacing: .5px; margin-top: 2px;
  }
  .contact-list {
    position: absolute; left: 600px; top: 232px;
    list-style: none;
  }
  .contact-item {
    display: flex; align-items: center; gap: 16px;
    font-size: 23px; color: var(--brand-orange);
    margin-bottom: 18px; letter-spacing: .3px;
  }
  .contact-icon { width: 24px; height: 20px; flex: none; }
  .divider {
    position: absolute; left: 0; right: 0; top: 392px; height: 10px;
    background: var(--divider-grey);
  }
  .services-band {
    position: absolute; left: 0; right: 0; top: 402px; bottom: 0;
    background: var(--brand-orange);
  }
  .services-label {
    position: absolute; left: 70px; top: 84px;
    background: var(--brand-navy);
    clip-path: polygon(3% 0, 100% 0, 97% 100%, 0 100%);
    padding: 12px 34px;
    color: var(--services-grey);
    font-weight: 700; font-size: 28px; text-transform: uppercase;
    letter-spacing: .5px;
  }
  .services-list {
    position: absolute; right: 60px; top: 30px;
    color: var(--services-grey);
    font-weight: 700; font-size: 28px; line-height: 1.25;
  }
</style>
</head>
<body>
  <article class="business-card">
    <div class="brand">
      <span class="brand-dot"></span>
      <span class="brand-name">Greenstripe<br>Yard Care</span>
    </div>

    <div class="holder">
      <p class="holder-name">Carl Whitby</p>
      <p class="holder-role">Designation</p>
    </div>

    <ul class="contact-list">
      <li class="contact-item">
        <svg class="contact-icon" viewBox="0 0 24 20" aria-hidden="true">
          <path d="M2 7c0-4 20-4 20 0v2h-5V7H7v2H2z" fill="#e0482e"/>
          <path d="M6 10h12l2 9H4z" fill="#e0482e"/>
          <circle cx="12" cy="14.5" r="2.3" fill="#f7f7f7"/>
        </svg>
        816-555-0147
      </li>
      <li class="contact-item">
        <svg class="contact-icon" viewBox="0 0 24 20" aria-hidden="true">
          <rect x="1" y="3" width="22" height="15" fill="#e0482e"/>
          <path d="M1 3l11 9 11-9" fill="none" stroke="#f7f7f7" stroke-width="1.6"/>
        </svg>
        greenstripeyard@fernmail.test
      </li>
    </ul>

    <div class="divider"></div>
    <section class="services-band">
      <p class="services-list">Mowing / Fertilization / Aeration<br>Bed &amp; tree Maintenance &amp; more.</p>
      <h2 class="services-label">Services Offered</h2>
    </section>
  </article>
</body>
</html>
```